National appliance rental company needs a newspaper ad design

We need an ad template that we can use for different newspaper advertising. Ad is to be colourful - I have attached our current marketing so you have an idea of colours.
Text to be something like the below:

Want it, Rent it, Own it!

Need to update your furniture? Kids need stuff for school?

(Put in pics of phones and TV)

Zelvos starting from just $8 per week
Smart phones starting from $10 per week
Large family fridges from $30 per week

TV’s, laptops, whitegoods, furniture, beds – we will finance just about anything!

Fast approvals – call 1300 582 967 or go to www.brightwellhomeleasing.com.au/apply - NOW!
$50 credit voucher given to the first 10 successful applicants.

(Pic of logo somewhere)
Terms and conditions apply. Pricing based on 24 month term

Brightwell Home Leasing P/L ACN 061 847 293. Australian Credit Licence # 718294

Target Market(s)

Low income people and families

Industry/Entity Type

Appliance

Requirements
Must have
• I would love to have a couple of different sizes.
• Maybe 6cm x 10 cm, and also 10cms x 10cms.
Nice to have
• Please use the green from fridge magnet and colours from our logo, etc.

```html
<!DOCTYPE html>
<html lang="en">
<head>
<meta charset="utf-8">
<title>Brightwell Home Leasing – Newspaper Ad</title>
<link href="https://fonts.googleapis.com/css2?family=Fredoka:wght@600;700&family=Arimo:ital,wght@0,400;0,700;1,400&display=swap" rel="stylesheet">
<style>
  :root {
    --page: #e9e6e1;
    --blue: #1a74b9;
    --red: #d92330;
    --green: #7cba3a;
    --yellow: #f9c616;
    --bright-yellow: #ffe600;
    --cream: #fdf6c9;
    --ink: #1f1f1f;
    --navy: #1c2f6b;
    --white: #ffffff;
  }
  * { box-sizing: border-box; margin: 0; padding: 0; }
  html, body { width: 1200px; height: 1000px; overflow: hidden; background: var(--page); }
  body { position: relative; font-family: "Arimo", Arial, sans-serif; }

  .ad {
    position: absolute; left: 302px; top: 35px; width: 556px; height: 928px;
    background: var(--cream); overflow: hidden;
  }
  .ad-backdrop { position: absolute; inset: 0; }

  .brand-mascot {
    position: absolute; left: 75px; top: 12px; width: 118px; height: 168px;
    border-radius: 14px;
    background: linear-gradient(160deg, #ffffff, #cfd6dc);
  }
  .brand-name {
    position: absolute; left: 205px; top: 44px; width: 250px;
    font-family: "Fredoka", Arial, sans-serif; font-weight: 700;
    font-size: 38px; line-height: 40px; color: var(--white);
  }
  .brand-tagline {
    position: absolute; left: 215px; top: 148px;
    font-style: italic; font-size: 15px; color: var(--navy);
  }

  .headline { position: absolute; left: 0; top: 180px; width: 556px; height: 120px; }
  .headline text {
    font-family: "Fredoka", Arial, sans-serif; font-weight: 700; font-size: 50px;
    fill: var(--red); stroke: var(--white); stroke-width: 7px;
    paint-order: stroke; stroke-linejoin: round;
  }

  .subhead {
    position: absolute; left: 0; top: 268px; width: 556px; text-align: center;
    font-weight: 700; font-size: 19px; line-height: 22px; color: var(--ink);
  }

  .product-photo {
    position: absolute; left: 43px; top: 318px; width: 145px; height: 294px;
    border-radius: 6px;
    background: linear-gradient(180deg, #2a2d33 0%, #3b4250 45%, #eef0f2 55%, #d3d7db 100%);
  }

  .offers { position: absolute; left: 243px; top: 326px; width: 313px; list-style: none; }
  .offer {
    height: 60px; margin-bottom: 9px; padding: 4px 0 0 36px;
    border: 3px solid var(--white); border-right: 0; border-radius: 12px 0 0 12px;
    color: var(--white); font-size: 22px; line-height: 25px;
    box-shadow: 2px 2px 4px rgba(0,0,0,.25);
  }
  .offer--red { background: var(--red); }
  .offer--blue { background: var(--blue); }
  .offer--green { background: var(--green); }
  .offer .price { color: var(--bright-yellow); font-weight: 700; font-size: 24px; }
  .offer::before { content: "•"; margin-left: -14px; margin-right: 6px; }

  .finance-box {
    position: absolute; left: 12px; top: 620px; width: 318px; height: 120px;
    background: var(--blue); border: 3px solid var(--white); border-radius: 12px;
    color: var(--white); font-size: 22px; line-height: 26px; text-align: center;
    padding-top: 6px; box-shadow: 2px 2px 4px rgba(0,0,0,.25);
  }

  .voucher {
    position: absolute; left: 326px; top: 534px; width: 234px; height: 234px;
    border-radius: 50%; background: var(--yellow); border: 4px solid var(--white);
    box-shadow: 0 2px 5px rgba(0,0,0,.3);
    display: flex; align-items: center; justify-content: center;
    padding: 0 8px; text-align: center;
    color: var(--red); font-weight: 700; font-size: 22px; line-height: 27px;
  }

  .cta {
    position: absolute; left: 0; top: 748px; width: 556px; height: 124px;
    background: var(--green); text-align: center; padding-top: 8px;
  }
  .cta-title, .cta-now {
    font-weight: 700; font-size: 28px; line-height: 30px; color: var(--red);
    -webkit-text-stroke: 1px var(--bright-yellow); paint-order: stroke;
  }
  .cta-line { font-size: 19px; line-height: 24px; color: var(--ink); }
  .cta-phone, .cta-url {
    font-weight: 700; color: var(--bright-yellow);
    -webkit-text-stroke: 3px var(--red); paint-order: stroke fill;
  }
  .cta-url { font-size: 20px; line-height: 24px; display: block; }

  .legal {
    position: absolute; left: 0; top: 873px; width: 556px; height: 55px;
    background: var(--red); color: var(--white); text-align: center;
    font-size: 12.5px; line-height: 17px; padding-top: 10px;
  }
</style>
</head>
<body>
  <article class="ad">
    <svg class="ad-backdrop" width="556" height="928" viewBox="0 0 556 928" aria-hidden="true">
      <rect width="556" height="230" fill="#1a74b9"/>
      <path d="M0 212 Q278 160 556 212 L556 928 L0 928 Z" fill="#fdf6c9"/>
      <path d="M-5 213 Q278 160 561 213" fill="none" stroke="#d92330" stroke-width="9"/>
    </svg>

    <header class="brand">
      <div class="brand-mascot" role="img" aria-label="Cartoon fridge mascot illustration"></div>
      <div class="brand-name">Brightwell Home Leasing</div>
      <p class="brand-tagline">“It’s easier to go Brightwell!”</p>
    </header>

    <svg class="headline" viewBox="0 0 556 120" role="heading" aria-level="1" aria-label="Want it, Rent it, Own it!">
      <defs><path id="headline-arc" d="M14 95 Q278 15 548 102"/></defs>
      <text><textPath href="#headline-arc" startOffset="50%" text-anchor="middle">Want it, Rent it, Own it!</textPath></text>
    </svg>

    <p class="subhead">Need to update your furniture?<br>Kids need stuff for school?</p>

    <div class="product-photo" role="img" aria-label="Photo of smartphones on a flat-screen TV above a front-loading washing machine"></div>

    <ul class="offers">
      <li class="offer offer--red">Zelvos starting from<br>just <span class="price">$8</span> per week</li>
      <li class="offer offer--blue">Smart phones starting<br>from <span class="price">$10</span> per week</li>
      <li class="offer offer--green">Large family fridges<br>from <span class="price">$30</span> per week</li>
    </ul>

    <p class="finance-box">TV’s, laptops, whitegoods,<br>furniture, beds –<br>we will finance just<br>about anything!</p>

    <p class="voucher">$50 credit<br>voucher given<br>to the first<br>10 successful<br>applicants.</p>

    <section class="cta">
      <p class="cta-title">FAST APPROVALS</p>
      <p class="cta-line">call <span class="cta-phone">1300 582 967</span> or go to</p>
      <span class="cta-url">www.brightwellhomeleasing.com.au/apply</span>
      <p class="cta-now">NOW!</p>
    </section>

    <footer class="legal">
      Terms and conditions apply. Pricing based on 24 month term<br>
      Brightwell Home Leasing P/L ACN 061 847 293. Australian Credit Licence # 718294
    </footer>
  </article>
</body>
</html>
```